Meadowrun Acres Website Design

We have been redeveloping our website already and are quite happy with the content, but the design needs to be better:
https://tilvexa-hub.examplehost.net/

Pages, content, concept etc. Can all be taken from the redeveloped website.
The farmer can register and edit/view their profile, subscribe and these pages need to be designed better as well as contact, about, pricing, tos, privacy and a page with example portlets.

We need a website to appeal to farmers, investors and retiring farmers.

The design should be clean and a little country.

We don't want any repeat designs that some may submit to every project and has no respect for the project brief, so please don't submit them.

Target Market(s)

farmers, investors, retirees

Industry/Entity Type

Farming

Number of Pages Required

5+ page

Colors

Designer to choose colors to be used in the design.

Requirements
Must have
• Nice, clean modern design that is appealing
• Profile page laid out nicely

```html
<!DOCTYPE html>
<html lang="en">
<head>
<meta charset="utf-8">
<title>Meadowrun Acres</title>
<link rel="stylesheet" href="https://fonts.googleapis.com/css2?family=Lato:wght@400;700;900&family=Open+Sans:ital,wght@0,400;0,600;0,700;1,400&display=swap">
<style>
:root{
  --green:#2f5d34;
  --green-dark:#244a29;
  --band:#34653b;
  --ink:#1f1f1f;
  --body:#6b6b6b;
  --muted:#8a8a8a;
  --line:#dcdcdc;
  --grey-bg:#f3f3f3;
  --white:#ffffff;
}
*{box-sizing:border-box;margin:0;padding:0}
html,body{width:1200px;height:3377px;overflow:hidden;background:var(--white)}
body{position:relative;font-family:"Open Sans",Arial,sans-serif;color:var(--body)}
.abs{position:absolute}
h2.section-title{position:absolute;left:0;width:1200px;text-align:center;font-family:"Lato",Arial,sans-serif;font-weight:900;font-size:27px;color:var(--ink);letter-spacing:.3px}

/* header */
.topline{left:0;top:0;width:1200px;height:4px;background:var(--green)}
.brand{left:98px;top:20px;display:flex;align-items:center;gap:12px;font-family:"Open Sans",sans-serif;font-weight:600;font-size:19px;color:var(--ink)}
.brand-dot{width:44px;height:44px;border-radius:50%;border:2px solid var(--green)}
.nav{left:351px;top:32px;display:flex;gap:21px;font-family:"Open Sans",sans-serif;font-size:14px;font-weight:600;color:#333;white-space:nowrap}
.nav a{color:#333;text-decoration:none}
.nav a.active{color:var(--green)}
.login{left:1006px;top:24px;width:94px;height:34px;border:1.5px solid #cfcfcf;border-radius:17px;font-family:"Lato",sans-serif;font-weight:700;font-size:13px;color:var(--green);display:flex;align-items:center;justify-content:center;gap:6px}

/* hero */
.hero{left:0;top:82px;width:1200px;height:438px;background:linear-gradient(180deg,#8aa2ad 0%,#5e7b58 28%,#6e7d3e 55%,#7a6d3a 80%,#5e5a2d 100%)}
.hero-title{left:0;top:188px;width:1200px;text-align:center;font-family:"Lato",sans-serif;font-weight:900;font-size:46px;color:var(--white)}
.hero-sub{left:0;top:250px;width:1200px;text-align:center;font-family:"Open Sans",sans-serif;font-weight:700;font-size:17px;color:var(--white)}
.hero-form{left:293px;top:303px;width:612px;height:98px;border:1px solid rgba(255,255,255,.8);background:rgba(255,255,255,.15)}
.hero-input{left:22px;top:24px;width:400px;height:52px;background:var(--white);font-size:12px;color:#555;padding-left:22px;line-height:52px;letter-spacing:.3px}
.hero-btn{left:412px;top:24px;width:178px;height:52px;border-radius:26px;background:var(--green);color:var(--white);font-family:"Lato",sans-serif;font-weight:900;font-size:17px;display:flex;align-items:center;justify-content:center}
.dots{left:562px;top:454px;display:flex;gap:6px}
.dots span{width:13px;height:13px;border-radius:50%;border:2px solid var(--white)}
.dots span.on{background:var(--white)}

/* welcome */
.lead{left:240px;top:634px;width:720px;text-align:center;font-size:12px;line-height:24px;color:var(--muted)}
.card{width:320px;text-align:center}
.card svg{display:block;margin:0 auto}
.card h3{margin-top:40px;font-family:"Lato",sans-serif;font-weight:900;font-size:18px;color:var(--ink)}
.card p{margin-top:16px;font-size:12px;line-height:22px;color:var(--muted)}
.card .more{display:block;margin-top:14px;font-family:"Lato",sans-serif;font-weight:900;font-size:12px;color:var(--green)}

/* own a farm */
.grey{left:0;width:1200px;background:var(--grey-bg)}
.own-title{left:99px;top:1166px;font-family:"Lato",sans-serif;font-weight:900;font-size:26px;color:var(--ink)}
.own-text{left:99px;top:1221px;width:460px;font-size:12px;line-height:23px;color:var(--muted)}
.own-text p+p{margin-top:22px}
.btn-ghost{height:38px;padding:0 18px;border:1.5px solid #c6c6c6;border-radius:19px;font-family:"Lato",sans-serif;font-weight:900;font-size:12px;color:var(--green);display:flex;align-items:center}
.video{left:590px;top:1160px;width:510px;height:314px;border:4px solid #dcdcdc;background:linear-gradient(135deg,#3f4650 0%,#6a4a4a 40%,#3c5c8c 70%,#2b2f3a 100%)}
.video-caption{left:14px;top:8px;font-size:12px;color:#e8e8e8}
.play{left:212px;top:114px;width:70px;height:70px;border-radius:50%;background:rgba(20,20,20,.85)}

/* how it works */
.step{width:200px;height:200px;border-radius:50%;border:1.5px solid #d6d6d6;background:var(--white)}
.step svg{position:absolute;left:50%;top:50%;transform:translate(-50%,-50%)}
.badge{width:40px;height:40px;border-radius:50%;background:#9a9a9a;color:var(--white);font-family:"Lato",sans-serif;font-weight:900;font-size:17px;display:flex;align-items:center;justify-content:center}
.step-label{width:300px;text-align:center;font-size:17px;line-height:27px;color:#333}

/* stats */
.stats-title{left:99px;top:2051px;font-family:"Lato",sans-serif;font-weight:900;font-size:26px;color:var(--ink)}
.ticks{left:99px;top:2107px;list-style:none;font-size:12px;color:#555}
.ticks li{display:flex;align-items:center;gap:14px;height:30px}

/* featured */
.partner{top:2522px;width:178px;height:84px;border:2px solid #dcdcdc;display:flex;align-items:center;justify-content:center;font-family:"Open Sans",sans-serif;font-weight:600;font-size:20px;color:#9a9a9a}
.arrow-btn{width:38px;height:38px;border-radius:50%;border:1.5px solid #cfcfcf;display:flex;align-items:center;justify-content:center}

/* testimonials */
.band{left:0;top:2684px;width:1200px;height:332px;background:var(--band)}
.band .section-title{color:var(--white);top:72px;font-size:26px}
.t-photo{width:76px;height:76px;border-radius:50%;border:3px solid var(--white);background:linear-gradient(180deg,#c9b3a0,#8d7766)}
.t-text{width:222px;font-size:11px;line-height:22px;font-style:italic;color:#e7efe6}
.t-name{margin-top:12px;font-style:normal;font-size:9px;color:#e7efe6;text-transform:uppercase;line-height:14px}
.t-name em{display:block;text-transform:none;font-size:9px}
.band-arrow{width:38px;height:38px;border-radius:50%;border:1.5px solid rgba(255,255,255,.8);display:flex;align-items:center;justify-content:center}

/* footer */
.f-col h4{font-family:"Open Sans",sans-serif;font-weight:700;font-size:16px;color:var(--ink);margin-bottom:14px}
.f-col ul{list-style:none;font-size:12px;color:#666;line-height:26px}
.f-mail{left:776px;top:3148px;width:230px;height:36px;border:1px solid #ccc;font-size:12px;color:#777;padding-left:14px;line-height:34px}
.f-sub{left:1006px;top:3148px;width:94px;height:36px;background:var(--green-dark);color:var(--white);font-family:"Lato",sans-serif;font-weight:900;font-size:12px;display:flex;align-items:center;justify-content:center}
.socials{left:776px;top:3240px;display:flex;gap:4px}
.socials span{width:32px;height:32px;border-radius:50%}
.copy{left:0;top:3329px;width:1200px;text-align:center;font-size:11px;color:#777}
.copy-rule{left:99px;top:3312px;width:1001px;height:1px;background:#e4e4e4}
</style>
</head>
<body>

<!-- header -->
<div class="abs topline"></div>
<div class="abs brand"><span class="brand-dot"></span>Meadowrun Acres</div>
<nav class="abs nav">
  <a class="active">Home</a>
  <a>Aspiring Farmers</a>
  <a>Investors</a>
  <a>Retiring Farmer</a>
  <a>Blog</a>
  <a>Pricing</a>
  <a>Contact</a>
</nav>
<svg class="abs" style="left:968px;top:32px" width="18" height="18" viewBox="0 0 18 18"><circle cx="7.5" cy="7.5" r="5.5" fill="none" stroke="#222" stroke-width="2.2"/><line x1="11.5" y1="11.5" x2="16" y2="16" stroke="#222" stroke-width="2.6" stroke-linecap="round"/></svg>
<div class="abs login"><svg width="10" height="12" viewBox="0 0 10 12"><rect x="0" y="5" width="10" height="7" rx="1" fill="#2f5d34"/><path d="M2.5 5V3.5a2.5 2.5 0 0 1 5 0V5" fill="none" stroke="#2f5d34" stroke-width="1.5"/></svg>LOGIN</div>

<!-- hero -->
<div class="abs hero" role="img" aria-label="Photo of a farmer on horseback herding cattle across a green paddock with wooded hills behind"></div>
<div class="abs hero-title">MEADOWRUN ACRES</div>
<div class="abs hero-sub">Subscribe to be Either an Aspiring or Premium Farmer to Receive</div>
<div class="abs hero-form">
  <div class="abs hero-input">ENTER YOUR EMAIL ADDRESS</div>
  <div class="abs hero-btn">GET STARTED</div>
</div>
<div class="abs dots"><span class="on"></span><span></span><span></span><span></span></div>

<!-- welcome -->
<h2 class="section-title" style="top:578px">WELCOME TO MEADOWRUN ACRES</h2>
<p class="abs lead">We know how hard it is for a young family to find the capital required to own and operate their own farm - so we started Meadowrun Acres. We want to rejuvenate regional Australia by putting farming back up the top of the career list for anyone.</p>

<div class="abs card" style="left:80px;top:758px">
  <svg width="80" height="76" viewBox="0 0 80 76"><circle cx="32" cy="18" r="14" fill="#2f5d34"/><path d="M6 72c0-20 11-32 26-32s26 12 26 32z" fill="#2f5d34"/><path d="M62 70c0-14 4-26 12-34" stroke="#2f5d34" stroke-width="3" fill="none"/><ellipse cx="66" cy="48" rx="4" ry="7" fill="#2f5d34" transform="rotate(-30 66 48)"/><ellipse cx="72" cy="40" rx="4" ry="7" fill="#2f5d34" transform="rotate(30 72 40)"/></svg>
  <h3>FARMERS</h3>
  <p>Our aim is to ensure that you are equity owner,<br>receive a wage and annual incentives, and have the<br>ongoing support of farming experts.</p>
  <span class="more">READ MORE &gt;&gt;</span>
</div>
<div class="abs card" style="left:440px;top:758px">
  <svg width="80" height="76" viewBox="0 0 80 76"><circle cx="30" cy="20" r="13" fill="#2f5d34"/><path d="M6 72c0-20 10-32 24-32s24 12 24 32z" fill="#2f5d34"/><text x="60" y="22" font-family="Lato,sans-serif" font-weight="900" font-size="22" fill="#2f5d34">$</text><rect x="58" y="56" width="5" height="16" fill="#2f5d34"/><rect x="66" y="48" width="5" height="24" fill="#2f5d34"/><rect x="74" y="38" width="5" height="34" fill="#2f5d34"/></svg>
  <h3>INVESTORS</h3>
  <p>Our aim is to ensure that you are equity owner,<br>receive a wage and annual incentives, and have the<br>ongoing support of farming experts.</p>
  <span class="more">READ MORE &gt;&gt;</span>
</div>
<div class="abs card" style="left:800px;top:758px">
  <svg width="80" height="76" viewBox="0 0 80 76"><ellipse cx="40" cy="14" rx="22" ry="4" fill="#2f5d34"/><rect x="29" y="2" width="22" height="12" rx="3" fill="#2f5d34"/><circle cx="40" cy="26" r="11" fill="#2f5d34"/><path d="M14 72c0-20 11-32 26-32s26 12 26 32z" fill="#2f5d34"/></svg>
  <h3>RETIRING FARMERS</h3>
  <p>Our aim is to ensure that you are equity owner,<br>receive a wage and annual incentives, and have the<br>ongoing support of farming experts.</p>
  <span class="more">READ MORE &gt;&gt;</span>
</div>

<!-- own a farm -->
<div class="abs grey" style="top:1105px;height:418px"></div>
<div class="abs own-title">YOU CAN OWN A FARM</div>
<div class="abs own-text">
  <p>We know how hard it is for a young family to find the capital required to own and operate their own farm - so we started Meadowrun Acres.</p>
  <p>We want to rejuvenate regional Australia by putting farming back up the top of the career list for anyone. Our focus will be to ensure you have a great farm experience, so we will be with you the whole way. We advocate for you to government, industry and to the public in order to help.</p>
</div>
<div class="abs btn-ghost" style="left:99px;top:1420px">READ MORE &gt;&gt;</div>
<div class="abs video" role="img" aria-label="Video still of a presenter speaking in a machinery shed beside a tractor">
  <div class="abs video-caption">Farm tour from Meadowrun Acres</div>
  <div class="abs play"><svg width="70" height="70" viewBox="0 0 70 70"><path d="M28 22l20 13-20 13z" fill="#fff"/></svg></div>
</div>

<!-- how it works -->
<h2 class="section-title" style="top:1586px">HOW MEADOWRUN ACRES WORKS</h2>
<svg class="abs" style="left:0;top:1740px" width="1200" height="30" viewBox="0 0 1200 30">
  <g stroke="#c8c8c8" stroke-width="1.5" stroke-dasharray="5 4" fill="none"><line x1="336" y1="15" x2="503" y2="15"/><line x1="703" y1="15" x2="863" y2="15"/></g>
  <g fill="none" stroke="#bdbdbd" stroke-width="3"><path d="M410 8l8 7-8 7"/><path d="M776 8l8 7-8 7"/></g>
</svg>
<div class="abs step" style="left:136px;top:1655px">
  <svg width="72" height="72" viewBox="0 0 72 72"><rect x="6" y="14" width="48" height="50" rx="8" fill="none" stroke="#2f5d34" stroke-width="6"/><path d="M28 44l4-12 26-26 8 8-26 26z" fill="#2f5d34"/></svg>
</div>
<div class="abs badge" style="left:292px;top:1670px">1</div>
<div class="abs step" style="left:503px;top:1655px">
  <svg width="80" height="76" viewBox="0 0 80 76"><g fill="#2f5d34"><circle cx="30" cy="40" r="18"/><g transform="translate(30 40)"><rect x="-5" y="-26" width="10" height="52"/><rect x="-5" y="-26" width="10" height="52" transform="rotate(45)"/><rect x="-5" y="-26" width="10" height="52" transform="rotate(90)"/><rect x="-5" y="-26" width="10" height="52" transform="rotate(135)"/></g><circle cx="62" cy="18" r="10"/><g transform="translate(62 18)"><rect x="-3" y="-15" width="6" height="30"/><rect x="-3" y="-15" width="6" height="30" transform="rotate(60)"/><rect x="-3" y="-15" width="6" height="30" transform="rotate(120)"/></g></g><circle cx="30" cy="40" r="7" fill="#fff"/><circle cx="62" cy="18" r="4" fill="#fff"/></svg>
</div>
<div class="abs badge" style="left:659px;top:1670px">2</div>
<div class="abs step" style="left:863px;top:1655px">
  <svg width="84" height="70" viewBox="0 0 84 70"><g fill="#2f5d34"><circle cx="42" cy="16" r="12"/><path d="M22 62c0-16 9-26 20-26s20 10 20 26z"/><circle cx="16" cy="22" r="9"/><path d="M0 60c0-12 7-20 16-20 3 0 5 1 7 2-3 5-5 11-5 18z"/><circle cx="68" cy="22" r="9"/><path d="M84 60c0-12-7-20-16-20-3 0-5 1-7 2 3 5 5 11 5 18z"/></g></svg>
</div>
<div class="abs badge" style="left:1019px;top:1670px">3</div>
<div class="abs step-label" style="left:165px;top:1868px">Register as an<br>Aspiring Farmer</div>
<div class="abs step-label" style="left:453px;top:1868px">Build your farm skills to get<br>yourself farm-ready.</div>
<div class="abs step-label" style="left:813px;top:1868px">Together we find you your<br>dream farm.</div>

<!-- statistics -->
<div class="abs grey" style="top:1998px;height:387px"></div>
<div class="abs stats-title">MEADOWRUN ACRES STATISTICS</div>
<ul class="abs ticks">
  <li><svg width="14" height="14" viewBox="0 0 14 14"><circle cx="7" cy="7" r="7" fill="#2f5d34"/><path d="M3.5 7.2l2.3 2.3 4.7-4.7" stroke="#fff" stroke-width="1.8" fill="none"/></svg>Free Tallyfield market analysis membership (valued at $300 pa)</li>
  <li><svg width="14" height="14" viewBox="0 0 14 14"><circle cx="7" cy="7" r="7" fill="#2f5d34"/><path d="M3.5 7.2l2.3 2.3 4.7-4.7" stroke="#fff" stroke-width="1.8" fill="none"/></svg>Farm business webinars (valued at $200)</li>
  <li><svg width="14" height="14" viewBox="0 0 14 14"><circle cx="7" cy="7" r="7" fill="#2f5d34"/><path d="M3.5 7.2l2.3 2.3 4.7-4.7" stroke="#fff" stroke-width="1.8" fill="none"/></svg>Corporate Partner Opportunities</li>
  <li><svg width="14" height="14" viewBox="0 0 14 14"><circle cx="7" cy="7" r="7" fill="#2f5d34"/><path d="M3.5 7.2l2.3 2.3 4.7-4.7" stroke="#fff" stroke-width="1.8" fill="none"/></svg>Public or Private profile (as required)</li>
  <li><svg width="14" height="14" viewBox="0 0 14 14"><circle cx="7" cy="7" r="7" fill="#2f5d34"/><path d="M3.5 7.2l2.3 2.3 4.7-4.7" stroke="#fff" stroke-width="1.8" fill="none"/></svg>Eligible to enter competitions and win prizes</li>
</ul>
<div class="abs btn-ghost" style="left:99px;top:2261px">READ MORE &gt;&gt;</div>

<svg class="abs" style="left:600px;top:2040px" width="600" height="290" viewBox="0 0 600 290" font-family="Open Sans,sans-serif">
  <g transform="translate(300 112)">
    <path d="M280,0 A280,105 0 0 1 140,90.9 L140,140.9 A280,105 0 0 0 280,50 Z" fill="#5e4789"/>
    <path d="M140,90.9 A280,105 0 0 1 -140,90.9 L-140,140.9 A280,105 0 0 0 140,140.9 Z" fill="#45593a"/>
    <path d="M-140,90.9 A280,105 0 0 1 -275.7,18.2 L-275.7,68.2 A280,105 0 0 0 -140,140.9 Z" fill="#4f8459"/>
    <path d="M-275.7,18.2 A280,105 0 0 1 -280,0 L-280,50 A280,105 0 0 0 -275.7,68.2 Z" fill="#4f5496"/>
    <g stroke="#ffffff" stroke-opacity=".35" stroke-width="1">
      <path d="M0,0 L-140,-90.9 A280,105 0 0 1 48.6,-103.4 Z" fill="#b5715c"/>
      <path d="M0,0 L48.6,-103.4 A280,105 0 0 1 214.5,-67.5 Z" fill="#b39b65"/>
      <path d="M0,0 L214.5,-67.5 A280,105 0 0 1 275.7,-18.2 Z" fill="#4ea4ae"/>
      <path d="M0,0 L275.7,-18.2 A280,105 0 0 1 140,90.9 Z" fill="#7c60b2"/>
      <path d="M0,0 L140,90.9 A280,105 0 0 1 -140,90.9 Z" fill="#5f7b50"/>
      <path d="M0,0 L-140,90.9 A280,105 0 0 1 -275.7,18.2 Z" fill="#6bab77"/>
      <path d="M0,0 L-275.7,18.2 A280,105 0 0 1 -140,-90.9 Z" fill="#6a70c0"/>
    </g>
    <g fill="#ffffff" font-size="14" text-anchor="middle">
      <text x="-40" y="-78">Milk</text><text x="-40" y="-59" font-weight="700">$50,248</text>
      <text x="70" y="-80">Grains</text><text x="70" y="-61" font-weight="700">$50,248</text>
      <text x="226" y="-48">Eggs</text><text x="226" y="-30" font-weight="700">$50,248</text>
      <text x="192" y="12">other slaughter of</text><text x="192" y="29">animals</text><text x="192" y="48" font-weight="700">$50,248</text>
      <text x="4" y="44">Sheep</text><text x="4" y="63" font-weight="700">$50,248</text>
      <text x="-150" y="40">Chicken</text><text x="-150" y="59" font-weight="700">$50,248</text>
      <text x="-176" y="-44">Slaughtering of</text><text x="-176" y="-27">livestock</text><text x="-176" y="-8" font-weight="700">$50,248</text>
    </g>
  </g>
</svg>

<!-- featured -->
<h2 class="section-title" style="top:2448px">AS FEATURED IN</h2>
<div class="abs arrow-btn" style="left:28px;top:2545px"><svg width="10" height="14" viewBox="0 0 10 14"><path d="M8 1L2 7l6 6" stroke="#aaa" stroke-width="2" fill="none"/></svg></div>
<div class="abs partner" style="left:99px">Pravik</div>
<div class="abs partner" style="left:305px">Delmora</div>
<div class="abs partner" style="left:511px">Quenpio</div>
<div class="abs partner" style="left:717px">Soarvane</div>
<div class="abs partner" style="left:923px">Earnwick</div>
<div class="abs arrow-btn" style="left:1132px;top:2545px"><svg width="10" height="14" viewBox="0 0 10 14"><path d="M2 1l6 6-6 6" stroke="#aaa" stroke-width="2" fill="none"/></svg></div>

<!-- testimonials -->
<section class="abs band">
  <h2 class="section-title">CLIENT TESTIMONIALS</h2>
  <div class="abs band-arrow" style="left:26px;top:143px"><svg width="10" height="14" viewBox="0 0 10 14"><path d="M8 1L2 7l6 6" stroke="#fff" stroke-width="2" fill="none"/></svg></div>
  <div class="abs band-arrow" style="left:1136px;top:143px"><svg width="10" height="14" viewBox="0 0 10 14"><path d="M2 1l6 6-6 6" stroke="#fff" stroke-width="2" fill="none"/></svg></div>

  <div class="abs t-photo" style="left:97px;top:120px" role="img" aria-label="Portrait photo of Marla Quinton"></div>
  <div class="abs t-text" style="left:190px;top:116px">&#8220; Land access is a major barrier to growing more farmers, and we are really excited to see the development of things like Meadowrun Acres..
    <div class="t-name">Marla Quinton<em>Quinton Farms, Elmbrook Victoria</em></div></div>

  <div class="abs t-photo" style="left:441px;top:120px" role="img" aria-label="Portrait photo of Dale Fenwick"></div>
  <div class="abs t-text" style="left:534px;top:116px">&#8220; Meadowrun Acres can offer an opportunity to put people with the skills and ambition, with either a farming family looking to transition into retirement ..
    <div class="t-name">Dale Fenwick<em>aspiring farmer, Redgum Queensland</em></div></div>

  <div class="abs t-photo" style="left:794px;top:120px" role="img" aria-label="Portrait photo of Owen Pratt"></div>
  <div class="abs t-text" style="left:887px;top:116px">&#8220; We both like the idea that Meadowrun Acres could have the ability to get more young people into small rural areas. We both love rural Australia
    <div class="t-name">Owen Pratt and Lachlan Reyes<em>aspiring farmers, Birchvale NSW</em></div></div>
</section>

<!-- footer -->
<div class="abs f-col" style="left:99px;top:3074px"><h4>Information</h4><ul><li>About Us</li><li>Careers</li><li>Privacy &amp; Security</li><li>Site Map</li><li>Terms of Use</li><li>Blog</li></ul></div>
<div class="abs f-col" style="left:262px;top:3074px"><h4>Get Started</h4><ul><li>Farmers</li><li>Investors</li><li>Retiring</li><li>About</li><li>Pricing</li></ul></div>
<div class="abs f-col" style="left:428px;top:3074px"><h4>Features</h4><ul><li>How it works</li><li>Our Story</li><li>Team</li><li>Newsletters</li><li>Contact</li><li>Jobs</li><li>Help Us Grow</li></ul></div>
<div class="abs f-col" style="left:604px;top:3074px"><h4>Resources</h4><ul><li>Customer Stories</li><li>Help Center</li><li>Resource Center</li><li>Product Guides</li><li>Tools</li></ul></div>
<div class="abs f-col" style="left:776px;top:3074px"><h4>Email Subscription</h4><ul><li>Register your email address to get information about us</li></ul></div>
<div class="abs f-mail">Email Address</div>
<div class="abs f-sub">SUBSCRIBE</div>
<div class="abs f-col" style="left:776px;top:3202px"><h4>Stay Connected</h4></div>
<div class="abs socials">
  <span style="background:#5fae7a"></span><span style="background:#3b5b98"></span><span style="background:#4ab3e8"></span><span style="background:#d8503f"></span><span style="background:#4f7ea8"></span><span style="background:#3aa0d8"></span><span style="background:#d42b2b"></span><span style="background:#c8232c"></span>
</div>
<div class="abs copy-rule"></div>
<div class="abs copy">Copyrights &#169; 2017, Meadowrun Acres. All Rights Reserved &nbsp;|&nbsp; Privacy Policy | Terms of Use | Feedback</div>

</body>
</html>
```